Income Tax Flyer - Updates Needed

Just need to update this flyer design and give it a new look. We would like to keep all the same wording but make it stand out a little more. Our selling point is the "Same Day Tax Advance up to $6,000"

Lending, Small Loans, Tax Services, Title Loans, Personal Loans

```html
<!DOCTYPE html>
<html lang="en">
<head>
<meta charset="utf-8">
<title>Same Day Tax Advance Flyer</title>
<link rel="stylesheet" href="https://fonts.googleapis.com/css2?family=Anton&family=Montserrat:wght@500;700;800;900&family=Poppins:wght@400;600;700&display=swap">
<style>
:root{
  --green:#17633a;
  --green-dark:#0f4d2b;
  --green-bright:#1ea653;
  --red:#c9202b;
  --ink:#1b1b1b;
  --paper:#ffffff;
  --bg:#ececec;
}
*{margin:0;padding:0;box-sizing:border-box}
html,body{width:1200px;height:2700px;overflow:hidden;background:var(--bg)}
.canvas{position:relative;width:1200px;height:2700px}
.flyer{
  position:absolute;left:50px;top:503px;width:1100px;height:1693px;
  background:radial-gradient(ellipse at 50% 45%,#ffffff 0%,#f7f7f7 55%,#ececec 100%);
  overflow:hidden;box-shadow:0 20px 50px rgba(0,0,0,.25);
  font-family:"Montserrat",sans-serif;
}
.brand{position:absolute;top:120px;left:0;width:100%;display:flex;justify-content:center;align-items:center;gap:18px}
.brand-dot{width:30px;height:30px;border-radius:50%;background:var(--red)}
.brand-name{font-family:"Montserrat",sans-serif;font-weight:700;font-size:44px;color:var(--green)}
.hero-photo{
  position:absolute;left:310px;top:240px;width:485px;height:235px;
  border-radius:160px 160px 18px 18px;
  background:linear-gradient(180deg,#5a3a2a 0%,#c98f6a 55%,#d9a07a 100%);
}
.headline{position:absolute;left:0;width:100%;text-align:center;font-family:"Montserrat",sans-serif;font-weight:900;letter-spacing:-3px;line-height:1;white-space:nowrap}
.headline-main{top:467px;font-size:176px;color:var(--green)}
.headline-sub{top:625px;font-size:123px;color:var(--red)}
.amount-box{position:absolute;left:175px;top:761px;width:769px;height:253px;border:3px solid var(--ink);border-left:none}
.amount-box::before{content:"";position:absolute;left:0;top:0;width:3px;height:22px;background:var(--ink)}
.amount-box::after{content:"";position:absolute;left:0;bottom:0;width:3px;height:22px;background:var(--ink)}
.up-to{position:absolute;left:136px;top:780px;height:214px;writing-mode:vertical-rl;transform:rotate(180deg);
  font-family:"Montserrat",sans-serif;font-weight:900;font-size:60px;line-height:1;color:var(--ink);text-align:center;white-space:nowrap}
.amount{position:absolute;left:240px;top:752px;font-family:"Anton",sans-serif;font-size:236px;line-height:1.1;letter-spacing:2px;white-space:nowrap;
  background:linear-gradient(90deg,var(--green-dark) 0%,var(--green-bright) 50%,var(--green-dark) 100%);
  -webkit-background-clip:text;background-clip:text;color:transparent}
.tagline{position:absolute;top:1036px;left:0;width:100%;text-align:center;font-family:"Poppins",sans-serif;font-size:46px;line-height:1.2;color:var(--ink)}
.tagline-accent{position:absolute;top:1086px;left:0;width:100%;text-align:center;font-family:"Poppins",sans-serif;font-weight:700;font-size:56px;line-height:1.2;color:var(--red)}
.features{position:absolute;top:1172px;left:88px;width:924px;display:flex;justify-content:space-between}
.feature{position:relative;width:278px;height:240px}
.feature-card{position:absolute;left:0;bottom:0;width:278px;height:178px;border-radius:24px;display:flex;align-items:flex-end;justify-content:center;padding-bottom:30px;
  font-family:"Poppins",sans-serif;font-weight:700;font-size:30px;line-height:1.25;color:#fff;text-align:center}
.feature-card.green{background:var(--green)}
.feature-card.red{background:var(--red)}
.feature-icon{position:absolute;left:77px;top:0;width:124px;height:124px;border-radius:50%;border:6px solid #fff;display:flex;align-items:center;justify-content:center}
.feature-icon.red{background:var(--red)}
.feature-icon.green{background:var(--green)}
.footer-curve{position:absolute;left:0;top:1420px;width:1100px;height:273px}
.contact{position:absolute;left:88px;top:1538px;color:#fff}
.contact-label{font-family:"Poppins",sans-serif;font-weight:700;font-size:36px;line-height:1.2}
.contact-phone{display:flex;align-items:center;gap:10px;margin-top:6px;font-family:"Poppins",sans-serif;font-weight:700;font-size:46px;line-height:1.2;white-space:nowrap}
.location{position:absolute;left:580px;top:1530px;color:#fff;font-family:"Poppins",sans-serif;font-size:34px;line-height:1.2;white-space:nowrap}
.location-name{display:flex;align-items:center;gap:14px;font-weight:700;font-size:36px;margin-left:-38px}
.location p{margin:0}
</style>
</head>
<body>
<div class="canvas">
  <div class="flyer">
    <div class="brand"><span class="brand-dot"></span><span class="brand-name">Harbor Lane Financial Group</span></div>

    <div class="hero-photo" role="img" aria-label="Photo of a smiling woman leaning over the headline and pointing down at it, with dollar bills falling around her"></div>

    <h1 class="headline headline-main">SAME DAY</h1>
    <h2 class="headline headline-sub">TAX ADVANCE</h2>

    <div class="amount-box"></div>
    <div class="up-to">UP TO</div>
    <div class="amount">$6,000</div>

    <p class="tagline">File your taxes and apply for an</p>
    <p class="tagline-accent">Easy Advance!</p>

    <div class="features">
      <div class="feature">
        <div class="feature-card green">Available In 24<br>Hours or Less</div>
        <div class="feature-icon red">
          <svg width="64" height="64" viewBox="0 0 64 64" fill="none" stroke="#fff" stroke-width="4">
            <path d="M18 22h18l6 10v18a6 6 0 0 1-6 6H18a6 6 0 0 1-6-6V32z"/><path d="M20 12h14l-4 10h-6z"/>
            <circle cx="46" cy="44" r="12" fill="#c9202b"/><path d="M46 37v7l5 3"/>
          </svg>
        </div>
      </div>
      <div class="feature">
        <div class="feature-card red">Choose Your<br>Loan Amount</div>
        <div class="feature-icon green">
          <svg width="64" height="64" viewBox="0 0 64 64" fill="none" stroke="#fff" stroke-width="4">
            <circle cx="34" cy="20" r="13"/><text x="34" y="27" text-anchor="middle" fill="#fff" stroke="none" font-family="Poppins,sans-serif" font-weight="700" font-size="20">$</text>
            <path d="M6 46l10-6h14l10 4 14-8 4 4-18 14H16l-10-2"/>
          </svg>
        </div>
      </div>
      <div class="feature">
        <div class="feature-card green">Quick and<br>Easy</div>
        <div class="feature-icon red">
          <svg width="64" height="64" viewBox="0 0 64 64" fill="none" stroke="#fff" stroke-width="4">
            <rect x="16" y="10" width="28" height="44" rx="3" transform="rotate(-12 30 32)"/>
            <rect x="22" y="12" width="28" height="44" rx="3"/><circle cx="36" cy="34" r="7"/>
          </svg>
        </div>
      </div>
    </div>

    <svg class="footer-curve" viewBox="0 0 1100 273" preserveAspectRatio="none">
      <path d="M0 95 Q550 -10 1100 95 V273 H0 Z" fill="#c9202b"/>
      <path d="M0 105 Q550 20 1100 115 V273 H0 Z" fill="#17633a"/>
    </svg>

    <div class="contact">
      <p class="contact-label">Contact Us Today!</p>
      <p class="contact-phone">
        <svg width="42" height="42" viewBox="0 0 44 44"><circle cx="22" cy="22" r="21" fill="#fff"/><path d="M14 12l5 0 2 7-3 2a16 16 0 0 0 7 7l2-3 7 2v5c0 2-2 3-4 3A22 22 0 0 1 11 16c0-2 1-4 3-4z" fill="#c9202b"/></svg>
        (505) 555-0142
      </p>
    </div>

    <div class="location">
      <p class="location-name">
        <svg width="24" height="30" viewBox="0 0 24 30"><path d="M12 0a12 12 0 0 1 12 12c0 8-12 18-12 18S0 20 0 12A12 12 0 0 1 12 0z" fill="#c9202b"/><circle cx="12" cy="12" r="5" fill="#fff"/></svg>
        Austin – Riverside
      </p>
      <p>1820-4 Meadow Ridge Rd</p>
      <p>Austin, Texas 78745</p>
    </div>
  </div>
</div>
</body>
</html>
```